FunBrixo Business Card

We need a business card design for our company. We sell construction-themed amusement rides for kids.

Contact Information for Business Card

Contact info on business card should include:
Carl Dunning
Co-Founder & COO
(833) 571-FUNBRIX
Carl@funbrixo-demo.com
www.funbrixo-demo.com

```html
<!DOCTYPE html>
<html lang="en">
<head>
<meta charset="utf-8">
<title>FunBrixo Business Card</title>
<link href="https://fonts.googleapis.com/css2?family=Ultra&family=Ubuntu:wght@400;500;700&display=swap" rel="stylesheet">
<style>
  :root {
    --stage: #1f1f1f;
    --card: #0b0b0b;
    --orange: #f26a21;
    --amber: #f7a21b;
    --blue: #1ba7e0;
    --rule: #d9d9d9;
    --hat: #f2c230;
    --vest: #e2563a;
  }
  * { margin: 0; padding: 0; box-sizing: border-box; }
  html, body {
    width: 1200px; height: 900px; overflow: hidden;
    background: radial-gradient(ellipse at 60% 30%, #353535 0%, var(--stage) 70%);
    font-family: "Ubuntu", sans-serif;
  }
  .card {
    position: absolute;
    left: 270px;
    width: 660px; height: 377px;
    background: var(--card);
    box-shadow: 0 12px 30px rgba(0,0,0,0.6);
  }
  .card--back { top: 53px; }
  .card--front { top: 470px; }

  .mascots {
    position: absolute;
    left: 190px; top: 40px;
    width: 300px; height: 300px;
    border-radius: 12px;
    background: linear-gradient(180deg, var(--hat) 0%, #c4532b 40%, #2c3a6b 75%, #5a5a5a 100%);
    opacity: 0.85;
  }

  .brand {
    position: absolute;
    left: 96px; top: 46px;
    display: flex; align-items: center; gap: 18px;
  }
  .brand__name {
    font-family: "Ubuntu", sans-serif;
    font-weight: 700;
    font-size: 64px;
    color: var(--orange);
    letter-spacing: 1px;
  }
  .brand__dot {
    width: 34px; height: 34px; border-radius: 50%;
    background: var(--orange);
  }

  .accent {
    position: absolute;
    left: 44px; top: 176px;
    width: 8px; height: 44px;
    background: var(--blue);
  }
  .person {
    position: absolute;
    left: 76px; top: 168px;
  }
  .person__name {
    font-family: "Ultra", serif;
    font-size: 34px;
    color: var(--orange);
    line-height: 1.1;
  }
  .person__role {
    font-size: 20px;
    color: var(--amber);
    margin-top: 2px;
  }
  .rule {
    position: absolute;
    left: 76px; top: 262px;
    width: 540px; height: 2px;
    background: var(--rule);
  }
  .contacts {
    position: absolute;
    left: 68px; top: 278px;
    list-style: none;
  }
  .contacts li {
    display: flex; align-items: center; gap: 10px;
    font-size: 19px; color: var(--amber);
    line-height: 28px;
  }
  .contacts svg { width: 18px; height: 18px; flex: none; }
  .contacts .web-strong { font-weight: 700; }
</style>
</head>
<body>
  <section class="card card--back">
    <div class="mascots" role="img" aria-label="Cartoon pair of construction workers in yellow hard hats with arms crossed"></div>
  </section>

  <section class="card card--front">
    <div class="brand">
      <span class="brand__name">FunBrixo</span>
      <span class="brand__dot"></span>
    </div>

    <span class="accent"></span>
    <div class="person">
      <h1 class="person__name">Carl Dunning</h1>
      <p class="person__role">Co-Founder &amp; COO</p>
    </div>
    <span class="rule"></span>

    <ul class="contacts">
      <li>
        <svg viewBox="0 0 24 24" fill="none" stroke="var(--orange)" stroke-width="2"><path d="M5 3h4l2 5-2.5 1.5a11 11 0 0 0 6 6L16 13l5 2v4a2 2 0 0 1-2 2A16 16 0 0 1 3 5a2 2 0 0 1 2-2z"/></svg>
        (833) 571-FUNBRIX
      </li>
      <li>
        <svg viewBox="0 0 24 24" fill="none" stroke="var(--orange)" stroke-width="2"><rect x="3" y="5" width="18" height="14"/><path d="M3 5l9 8 9-8"/></svg>
        Carl@funbrixo-demo.com
      </li>
      <li>
        <svg viewBox="0 0 24 24" fill="none" stroke="var(--orange)" stroke-width="2"><circle cx="12" cy="12" r="9"/><path d="M3 12h18M12 3c3 3 3 15 0 18M12 3c-3 3-3 15 0 18"/></svg>
        <span>www.<span class="web-strong">funbrixo-demo</span>.com</span>
      </li>
    </ul>
  </section>
</body>
</html>
```